Website needed for modern mobile app developer for small business'

Hi

We are looking for someone to design a very modern looking website with company logo that outlines what our business is and let's users purchase a mobile app designed by our company. (For ideas think quillnest.example or ) The user should be able to describe what functionality they require and we will go and provide a test version of their app built

We would also like a testimonials page.

I currently have hosting on Brindle Hosting, so if this could be taken into account that would be great.
Updates

here is the logo - if colour scheme could match that would be great Added Wednesday, March 30, 2016

Target Market(s)

Small and medium business

Industry/Entity Type

Business

Number of Pages Required

3 page

Requirements
Must have
• Homepage who we are and what we offer
• Pricing page explaining the different products available - HTML5 app, Greenbot App or Pearphone app with an option to purchase
• A testimonials page
• A one that makes it easier for potential customers to get in contact.

```html
<!DOCTYPE html>
<html lang="en">
<head>
<meta charset="utf-8">
<title>Loftwell – Mobile App Developer</title>
<link href="https://fonts.googleapis.com/css2?family=Open+Sans:wght@400;600;700;800&family=Oswald:wght@500&display=swap" rel="stylesheet">
<style>
:root{
  --blue:#0b6bb5;
  --blue-dark:#095a99;
  --ink:#222;
  --text:#555;
  --muted:#888;
  --grey-bg:#f1f1f1;
  --line:#e6e6e6;
  --price:#d9502c;
  --footer:#3a3a3a;
  --white:#fff;
}
*{box-sizing:border-box;margin:0;padding:0}
html,body{width:1200px;height:2875px;overflow:hidden}
body{font-family:"Open Sans",Arial,sans-serif;color:var(--text);background:var(--white);position:relative}

/* header */
.site-header{position:absolute;top:0;left:0;width:1200px;height:70px;background:var(--white)}
.brand{position:absolute;left:160px;top:14px;font-size:30px;font-weight:400;color:var(--ink);letter-spacing:.5px}
.main-nav{position:absolute;left:427px;top:22px;display:flex;align-items:center;gap:6px;font-size:11px;font-weight:600;color:var(--ink);text-transform:uppercase}
.main-nav a{padding:6px 12px;color:inherit;text-decoration:none}
.main-nav a.active{background:var(--blue);color:var(--white)}
.nav-phone{display:flex;align-items:center;gap:8px;margin-left:6px;color:var(--blue);font-size:15px;font-weight:600;text-transform:none;white-space:nowrap}

/* hero */
.hero{position:absolute;top:70px;left:0;width:1200px;height:495px;background:linear-gradient(100deg,#dcdedf 0%,#c9ced3 40%,#aab4bf 70%,#44536a 100%)}
.hero-caption{position:absolute;left:160px;top:202px}
.hero-title{display:inline-block;background:rgba(60,60,60,.82);color:var(--white);font-size:25px;font-weight:700;padding:8px 14px;letter-spacing:.5px}
.hero-sub{display:inline-block;background:rgba(90,90,90,.82);color:var(--white);font-size:17px;font-weight:700;padding:6px 14px;margin-top:2px}
.hero-arrow{position:absolute;top:220px}
.hero-arrow.prev{left:58px}
.hero-arrow.next{right:58px}
.dots{display:flex;gap:12px;justify-content:center}
.dots span{width:9px;height:9px;border-radius:50%;background:var(--ink)}
.dots span.on{background:transparent;border:2px solid var(--blue)}
.hero .dots{position:absolute;top:458px;left:0;width:1200px}

/* split sections */
.split{position:absolute;left:0;width:1200px;height:407px;display:flex}
.split > div{width:600px;height:100%}
.who{top:565px}
.what{top:972px;height:408px}
.info{display:flex;flex-direction:column;align-items:center;padding-top:58px;text-align:center}
.info.grey{background:var(--grey-bg)}
.icon-ring{width:52px;height:52px;border:2px solid var(--blue);border-radius:50%;display:flex;align-items:center;justify-content:center;color:var(--blue);background:var(--white)}
.section-title{color:var(--blue);font-size:19px;font-weight:800;margin-top:16px;text-transform:uppercase}
.title-rule{width:76px;height:2px;background:var(--blue);margin-top:8px}
.info p{font-size:11.5px;line-height:21px;color:var(--text);width:370px;margin-top:20px}
.btn{display:inline-block;background:var(--blue);color:var(--white);font-size:10.5px;font-weight:700;text-transform:uppercase;padding:0 21px;line-height:32px}
.info .btn{margin-top:26px}
.photo-team{background:linear-gradient(160deg,#b8bcc1 0%,#8e949c 45%,#5d6470 100%)}
.photo-phone{background:linear-gradient(120deg,#cfc8bc 0%,#9c9a93 45%,#3d4a5a 75%,#7e8a96 100%)}

/* pricing */
.pricing{position:absolute;top:1380px;left:0;width:1200px;height:585px;background:var(--grey-bg);text-align:center}
.pricing .head{display:flex;flex-direction:column;align-items:center;padding-top:31px}
.pricing .section-title{margin-top:14px}
.plans{position:absolute;top:183px;left:162px;display:flex;gap:11px}
.plan{position:relative;width:285px;height:352px;background:var(--white);box-shadow:0 1px 6px rgba(0,0,0,.08);padding-top:52px}
.plan-badge{position:absolute;top:-38px;left:102px;width:80px;height:80px;border-radius:50%;background:var(--white);box-shadow:0 1px 6px rgba(0,0,0,.1);display:flex;align-items:center;justify-content:center}
.plan-badge span{width:40px;height:40px;border-radius:50%}
.plan h3{color:var(--blue);font-size:14px;font-weight:800;text-transform:uppercase}
.price{font-family:"Oswald",Arial,sans-serif;color:var(--price);font-size:25px;font-weight:500;margin-top:2px}
.features{list-style:none;text-align:left;margin:14px 24px 0}
.features li{display:flex;align-items:center;gap:14px;font-size:10.5px;color:var(--text);height:31.5px;border-bottom:1px solid var(--line)}
.features li:last-child{border-bottom:none}
.plan .btn{position:absolute;bottom:-18px;left:93px;width:100px;padding:0;font-size:12px;line-height:32px}

/* testimonials */
.testimonials{position:absolute;top:1965px;left:0;width:1200px;height:358px;background:linear-gradient(180deg,#2c3645 0%,#3e4a5a 40%,#222a36 100%);text-align:center;color:var(--white)}
.testimonials .head{display:flex;flex-direction:column;align-items:center;padding-top:34px}
.icon-ring.light{border-color:var(--white);background:transparent;color:var(--white)}
.testimonials .section-title{color:var(--white);margin-top:12px}
.title-rule.light{background:var(--white);width:54px}
.quote-mark{position:absolute;left:178px;top:138px}
.quote{width:770px;margin:18px auto 0;font-size:12.5px;font-weight:600;line-height:21px}
.author{display:flex;align-items:center;justify-content:center;gap:10px;margin-top:18px;text-align:left}
.avatar{width:40px;height:40px;border-radius:50%;background:linear-gradient(160deg,#c9b8a8,#5e6b7c);border:2px solid var(--white)}
.author strong{display:block;font-size:11px;font-weight:800;text-transform:uppercase}
.author small{font-size:10px}
.testimonials .dots{margin-top:24px}
.testimonials .dots span{background:var(--white)}
.testimonials .dots span.on{border-color:var(--white);background:transparent}

/* contact */
.contact{position:absolute;top:2323px;left:0;width:1200px;height:422px;background:var(--white)}
.contact .head{display:flex;flex-direction:column;align-items:center;padding-top:32px}
.contact .section-title{margin-top:12px}
.contact-form{position:absolute;top:165px;left:276px;width:653px;height:250px}
.field{position:absolute;left:0;width:321px;height:44px;border:1px solid #d8d8d8;display:flex;align-items:center;gap:14px;padding-left:14px;font-size:10px;color:var(--text);text-transform:uppercase}
.field.message{left:332px;top:0;height:154px;align-items:flex-start;padding-top:14px}
.submit{position:absolute;right:0;top:175px;width:114px;height:37px;background:var(--blue);color:var(--white);font-size:13px;font-weight:700;display:flex;align-items:center;justify-content:center;gap:8px;text-transform:uppercase}

/* footer */
.site-footer{position:absolute;top:2745px;left:0;width:1200px;height:130px;background:var(--footer);color:#ddd;font-size:10px}
.footer-links{position:absolute;left:160px;top:40px;display:flex;gap:8px}
.footer-links span.sep{color:#999}
.copyright{position:absolute;left:160px;top:64px}
.connect{position:absolute;right:160px;top:34px;text-align:right}
.socials{display:flex;gap:4px;justify-content:flex-end;margin-top:10px}
.socials span{width:20px;height:20px}
</style>
</head>
<body>

<header class="site-header">
  <div class="brand">Loftwell</div>
  <nav class="main-nav">
    <a class="active">Home</a>
    <a>Who we are</a>
    <a>Pricing</a>
    <a>Testimonials</a>
    <a>Contact us</a>
    <span class="nav-phone">
      <svg width="13" height="13" viewBox="0 0 24 24"><path fill="#0b6bb5" d="M6.6 10.8a15 15 0 0 0 6.6 6.6l2.2-2.2c.3-.3.7-.4 1-.2 1.1.4 2.3.6 3.6.6.6 0 1 .4 1 1V20c0 .6-.4 1-1 1A17 17 0 0 1 3 4c0-.6.4-1 1-1h3.5c.6 0 1 .4 1 1 0 1.3.2 2.5.6 3.6.1.3 0 .7-.2 1z"/></svg>
      1.800.555.0142
    </span>
  </nav>
</header>

<section class="hero" role="img" aria-label="Photo of a smiling business team working around a laptop in a bright office">
  <svg class="hero-arrow prev" width="26" height="44" viewBox="0 0 26 44"><path d="M22 4 6 22l16 18" fill="none" stroke="#9a9a9a" stroke-width="6"/></svg>
  <svg class="hero-arrow next" width="26" height="44" viewBox="0 0 26 44"><path d="M4 4l16 18L4 40" fill="none" stroke="#c9ccd0" stroke-width="6"/></svg>
  <div class="hero-caption">
    <div class="hero-title">MOBILE APP DEVELOPER</div><br>
    <div class="hero-sub">SMALL BUSINESS &amp; ENTERPRISES</div>
  </div>
  <div class="dots"><span></span><span class="on"></span><span></span><span></span><span></span></div>
</section>

<section class="split who">
  <div class="info grey">
    <div class="icon-ring">
      <svg width="24" height="20" viewBox="0 0 24 20"><g fill="#0b6bb5"><circle cx="12" cy="5" r="4"/><path d="M4 18c0-5 3.5-7 8-7s8 2 8 7z"/><circle cx="4.5" cy="6.5" r="2.6"/><circle cx="19.5" cy="6.5" r="2.6"/><path d="M0 16c0-3 2-4.5 4.5-4.5L3 16zM24 16c0-3-2-4.5-4.5-4.5L21 16z"/></g></svg>
    </div>
    <h2 class="section-title">Who we are</h2>
    <div class="title-rule"></div>
    <p>But I must explain to you how all this mistaken idea of denouncing pleasure and praising pain was born and I will give you a complete account of the system, and expound the actual teachings of the great explorer&nbsp; of the truth.</p>
    <span class="btn">Read more</span>
  </div>
  <div class="photo-team" role="img" aria-label="Photo of a confident business team in suits with arms crossed"></div>
</section>

<section class="split what">
  <div class="photo-phone" role="img" aria-label="Photo of a hand holding a smartphone showing the app on a blue screen"></div>
  <div class="info">
    <div class="icon-ring">
      <svg width="14" height="22" viewBox="0 0 14 22"><rect x="1" y="1" width="12" height="20" rx="2" fill="none" stroke="#0b6bb5" stroke-width="2"/><circle cx="7" cy="17.5" r="1.2" fill="#0b6bb5"/></svg>
    </div>
    <h2 class="section-title">What we do</h2>
    <div class="title-rule"></div>
    <p>But I must explain to you how all this mistaken idea of denouncing pleasure and praising pain was born and I will give you a complete account of the system, and expound the actual teachings of the great explorer&nbsp; of the truth.</p>
    <span class="btn">Read more</span>
  </div>
</section>

<section class="pricing">
  <div class="head">
    <div class="icon-ring"><span style="font-size:22px;font-weight:700">$</span></div>
    <h2 class="section-title">Pricing</h2>
    <div class="title-rule"></div>
  </div>
  <div class="plans">
    <article class="plan">
      <div class="plan-badge"><span style="background:#e44d26"></span></div>
      <h3>HTML5 App</h3>
      <div class="price">$56.99</div>
      <ul class="features">
        <li><svg width="10" height="10" viewBox="0 0 10 10"><circle cx="5" cy="5" r="5" fill="#0b6bb5"/><path d="M2.7 5.2l1.6 1.5 3-3.2" fill="none" stroke="#fff" stroke-width="1.3"/></svg>Lorem Ipsum is simply</li>
        <li><svg width="10" height="10" viewBox="0 0 10 10"><circle cx="5" cy="5" r="5" fill="#0b6bb5"/><path d="M2.7 5.2l1.6 1.5 3-3.2" fill="none" stroke="#fff" stroke-width="1.3"/></svg>Contrary to popular belie</li>
        <li><svg width="10" height="10" viewBox="0 0 10 10"><circle cx="5" cy="5" r="5" fill="#0b6bb5"/><path d="M2.7 5.2l1.6 1.5 3-3.2" fill="none" stroke="#fff" stroke-width="1.3"/></svg>There are many variations</li>
        <li><svg width="10" height="10" viewBox="0 0 10 10"><circle cx="5" cy="5" r="5" fill="#0b6bb5"/><path d="M2.7 5.2l1.6 1.5 3-3.2" fill="none" stroke="#fff" stroke-width="1.3"/></svg>The standard chunk of Lorem</li>
        <li><svg width="10" height="10" viewBox="0 0 10 10"><circle cx="5" cy="5" r="5" fill="#0b6bb5"/><path d="M2.7 5.2l1.6 1.5 3-3.2" fill="none" stroke="#fff" stroke-width="1.3"/></svg>Sed ut perspiciatis unde omnis</li>
        <li><svg width="10" height="10" viewBox="0 0 10 10"><circle cx="5" cy="5" r="5" fill="#0b6bb5"/><path d="M2.7 5.2l1.6 1.5 3-3.2" fill="none" stroke="#fff" stroke-width="1.3"/></svg>But I must explain to you</li>
      </ul>
      <span class="btn">Purchase</span>
    </article>
    <article class="plan">
      <div class="plan-badge"><span style="background:#8cc63f"></span></div>
      <h3>Greenbot App</h3>
      <div class="price">$66.99</div>
      <ul class="features">
        <li><svg width="10" height="10" viewBox="0 0 10 10"><circle cx="5" cy="5" r="5" fill="#0b6bb5"/><path d="M2.7 5.2l1.6 1.5 3-3.2" fill="none" stroke="#fff" stroke-width="1.3"/></svg>Lorem Ipsum is simply</li>
        <li><svg width="10" height="10" viewBox="0 0 10 10"><circle cx="5" cy="5" r="5" fill="#0b6bb5"/><path d="M2.7 5.2l1.6 1.5 3-3.2" fill="none" stroke="#fff" stroke-width="1.3"/></svg>Contrary to popular belie</li>
        <li><svg width="10" height="10" viewBox="0 0 10 10"><circle cx="5" cy="5" r="5" fill="#0b6bb5"/><path d="M2.7 5.2l1.6 1.5 3-3.2" fill="none" stroke="#fff" stroke-width="1.3"/></svg>There are many variations</li>
        <li><svg width="10" height="10" viewBox="0 0 10 10"><circle cx="5" cy="5" r="5" fill="#0b6bb5"/><path d="M2.7 5.2l1.6 1.5 3-3.2" fill="none" stroke="#fff" stroke-width="1.3"/></svg>The standard chunk of Lorem</li>
        <li><svg width="10" height="10" viewBox="0 0 10 10"><circle cx="5" cy="5" r="5" fill="#0b6bb5"/><path d="M2.7 5.2l1.6 1.5 3-3.2" fill="none" stroke="#fff" stroke-width="1.3"/></svg>Sed ut perspiciatis unde omnis</li>
        <li><svg width="10" height="10" viewBox="0 0 10 10"><circle cx="5" cy="5" r="5" fill="#0b6bb5"/><path d="M2.7 5.2l1.6 1.5 3-3.2" fill="none" stroke="#fff" stroke-width="1.3"/></svg>But I must explain to you</li>
      </ul>
      <span class="btn">Purchase</span>
    </article>
    <article class="plan">
      <div class="plan-badge"><span style="background:#7a7a7a"></span></div>
      <h3>Pearphone App</h3>
      <div class="price">$68.99</div>
      <ul class="features">
        <li><svg width="10" height="10" viewBox="0 0 10 10"><circle cx="5" cy="5" r="5" fill="#0b6bb5"/><path d="M2.7 5.2l1.6 1.5 3-3.2" fill="none" stroke="#fff" stroke-width="1.3"/></svg>Lorem Ipsum is simply</li>
        <li><svg width="10" height="10" viewBox="0 0 10 10"><circle cx="5" cy="5" r="5" fill="#0b6bb5"/><path d="M2.7 5.2l1.6 1.5 3-3.2" fill="none" stroke="#fff" stroke-width="1.3"/></svg>Contrary to popular belie</li>
        <li><svg width="10" height="10" viewBox="0 0 10 10"><circle cx="5" cy="5" r="5" fill="#0b6bb5"/><path d="M2.7 5.2l1.6 1.5 3-3.2" fill="none" stroke="#fff" stroke-width="1.3"/></svg>There are many variations</li>
        <li><svg width="10" height="10" viewBox="0 0 10 10"><circle cx="5" cy="5" r="5" fill="#0b6bb5"/><path d="M2.7 5.2l1.6 1.5 3-3.2" fill="none" stroke="#fff" stroke-width="1.3"/></svg>The standard chunk of Lorem</li>
        <li><svg width="10" height="10" viewBox="0 0 10 10"><circle cx="5" cy="5" r="5" fill="#0b6bb5"/><path d="M2.7 5.2l1.6 1.5 3-3.2" fill="none" stroke="#fff" stroke-width="1.3"/></svg>Sed ut perspiciatis unde omnis</li>
        <li><svg width="10" height="10" viewBox="0 0 10 10"><circle cx="5" cy="5" r="5" fill="#0b6bb5"/><path d="M2.7 5.2l1.6 1.5 3-3.2" fill="none" stroke="#fff" stroke-width="1.3"/></svg>But I must explain to you</li>
      </ul>
      <span class="btn">Purchase</span>
    </article>
  </div>
</section>

<section class="testimonials" role="img" aria-label="Blurred photo of business people walking through a glass office lobby">
  <div class="head">
    <div class="icon-ring light">
      <svg width="22" height="20" viewBox="0 0 22 20"><ellipse cx="11" cy="9" rx="10" ry="7.5" fill="#fff"/><path d="M4 14l-2 5 6-3z" fill="#fff"/><g fill="#3e4a5a"><circle cx="7" cy="9" r="1.3"/><circle cx="11" cy="9" r="1.3"/><circle cx="15" cy="9" r="1.3"/></g></svg>
    </div>
    <h2 class="section-title">Testimonials</h2>
    <div class="title-rule light"></div>
  </div>
  <svg class="quote-mark" width="38" height="30" viewBox="0 0 38 30"><g fill="#8a939e"><path d="M0 30V16C0 7 5 2 14 0l2 4c-5 2-7 5-7 10h7v16z"/><path d="M21 30V16c0-9 5-14 14-16l2 4c-5 2-7 5-7 10h7v16z"/></g></svg>
  <p class="quote">But I must explain to you how all this mistaken idea of denouncing pleasure and praising pain was born and I will give you a complete account of the system, and expound the actual teachings of the great explorer of the truth, the master-builder of human happiness. No one rejects, dislikes, or avoids pleasure itself, because it is pleasure</p>
  <div class="author">
    <div class="avatar" role="img" aria-label="Portrait of the client"></div>
    <div><strong>Marcus Delane</strong><small>Australia</small></div>
  </div>
  <div class="dots"><span></span><span></span><span class="on"></span><span></span><span></span></div>
</section>

<section class="contact">
  <div class="head">
    <div class="icon-ring">
      <svg width="14" height="22" viewBox="0 0 14 22"><rect x="1" y="1" width="12" height="20" rx="2" fill="none" stroke="#0b6bb5" stroke-width="2"/><circle cx="7" cy="17.5" r="1.2" fill="#0b6bb5"/></svg>
    </div>
    <h2 class="section-title">Contact us</h2>
    <div class="title-rule"></div>
  </div>
  <form class="contact-form">
    <div class="field" style="top:0">
      <svg width="10" height="11" viewBox="0 0 10 11"><circle cx="5" cy="3" r="2.6" fill="#333"/><path d="M0 11c0-4 2-5.5 5-5.5S10 7 10 11z" fill="#333"/></svg>Name</div>
    <div class="field" style="top:55px">
      <svg width="11" height="9" viewBox="0 0 11 9"><rect width="11" height="9" fill="#333"/><path d="M0 0l5.5 4.5L11 0" fill="none" stroke="#fff" stroke-width="1"/></svg>E mail</div>
    <div class="field" style="top:110px">
      <svg width="10" height="10" viewBox="0 0 24 24"><path fill="#333" d="M6.6 10.8a15 15 0 0 0 6.6 6.6l2.2-2.2c.3-.3.7-.4 1-.2 1.1.4 2.3.6 3.6.6.6 0 1 .4 1 1V20c0 .6-.4 1-1 1A17 17 0 0 1 3 4c0-.6.4-1 1-1h3.5c.6 0 1 .4 1 1 0 1.3.2 2.5.6 3.6.1.3 0 .7-.2 1z"/></svg>Phone</div>
    <div class="field message">
      <svg width="11" height="11" viewBox="0 0 11 11"><rect x=".5" y="1.5" width="9" height="9" fill="none" stroke="#333"/><path d="M4 7l6-6" stroke="#333" stroke-width="1.5"/></svg>Message</div>
    <div class="submit">Submit
      <svg width="14" height="10" viewBox="0 0 14 10"><path d="M0 5h12M8 1l4 4-4 4" fill="none" stroke="#fff" stroke-width="2"/></svg>
    </div>
  </form>
</section>

<footer class="site-footer">
  <div class="footer-links">
    <span>Home</span><span class="sep">|</span><span>Who we are</span><span class="sep">|</span><span>Pricing</span><span class="sep">|</span><span>Testimoanils</span><span class="sep">|</span><span>Contact Us</span>
  </div>
  <div class="copyright">Copyrights @ 2016 All Rights Reserved</div>
  <div class="connect">Connect With Us
    <div class="socials">
      <span style="background:#3b5998"></span><span style="background:#1da1f2"></span><span style="background:#dd4b39"></span><span style="background:#0077b5"></span>
    </div>
  </div>
</footer>

</body>
</html>
```